4th Generation Family Business Needs a New Card Design!

We are a family owned 4th Generation company. We are based in the Sydney, Australia area and we are desperately in need of a more modern and classy card. We are monumental masons who design, supply & erect lasting memorials throughout cemeteries in Sydney. Our customers are normally in a period of grieving. I have attached logo files that will need to be implemented on the card. Company was established 1935. Australian Owned and Operated. Card needs to be designed to PIXO.com specification.

Target Market(s)

Our target market is based upon people that a grieving for family members that have passed away. We also deal with alot of companies that own and operate cemeteries.

Industry/Entity Type

Business

Contact Information for Business Card

Simon Harcourt, Operations Manager, 0417293086, simon@harcourtmemorials.com.au
Lewis Harcourt, Director, 0491630572, lewis@harcourtmemorials.com.au
Phone # 02 9561 3048
Website: www.harcourtmemorials.com.au
Address: Suite 17, 8 Palfrey Lane, West Carlow, Sydney NSW 2156

Font styles to use
Serif
Decorative
Script

Requirements
Must have
• Would like to see the logo nicely implemented with a modern design. Embossed lettering would be a nice additive.

```html
<!DOCTYPE html>
<html lang="en">
<head>
<meta charset="utf-8">
<title>Harcourt Memorials – Business Card</title>
<link rel="stylesheet" href="https://fonts.googleapis.com/css2?family=Cinzel:wght@400;600&family=Open+Sans:wght@400;600&display=swap">
<style>
  :root {
    --bg-light: #8a8a8a;
    --bg-dark: #3a3a3a;
    --card: #ffffff;
    --ink: #1e1e1e;
    --gold: #e2b71c;
    --gold-soft: #fbf1cf;
    --grey-soft: #e6e6e6;
    --text-grey: #555555;
    --band: #262626;
  }
  * { margin: 0; padding: 0; box-sizing: border-box; }
  html, body { width: 1200px; height: 950px; overflow: hidden; }
  body {
    background: radial-gradient(ellipse at 45% 40%, var(--bg-light), var(--bg-dark) 85%);
    position: relative;
    font-family: "Open Sans", Arial, sans-serif;
  }
  .card {
    position: absolute;
    width: 630px;
    height: 360px;
    background: var(--card);
    box-shadow: 0 18px 40px rgba(0,0,0,0.45);
    overflow: hidden;
  }
  /* Front */
  .card--front { left: 110px; top: 80px; }
  .front-decoration {
    position: absolute;
    left: 40px; top: 30px;
    width: 300px; height: 300px;
    background: var(--grey-soft);
    opacity: 0.7;
  }
  .front-wordmark {
    position: absolute;
    right: 48px; top: 150px;
    text-align: center;
  }
  .wordmark-name {
    font-family: "Cinzel", Georgia, serif;
    font-weight: 600;
    color: var(--ink);
    letter-spacing: 1px;
    line-height: 1.05;
  }
  .front-wordmark .wordmark-name { font-size: 30px; }
  .front-wordmark .wordmark-rule { height: 2px; background: var(--gold); margin: 8px 0 6px; }
  .front-wordmark .site { font-size: 15px; color: var(--text-grey); letter-spacing: 0.5px; }

  /* Back */
  .card--back { left: 460px; top: 500px; }
  .back-brand {
    position: absolute;
    left: 40px; top: 78px;
    width: 250px;
    display: flex; align-items: center; gap: 12px;
  }
  .brand-square { width: 22px; height: 22px; background: var(--gold); flex: none; }
  .back-brand .wordmark-name { font-size: 25px; }
  .brand-rule { position: absolute; left: 40px; top: 150px; width: 250px; height: 2px; background: var(--gold); }
  .person { position: absolute; left: 40px; top: 210px; }
  .person-name {
    font-family: "Cinzel", Georgia, serif;
    font-size: 24px; color: var(--ink); letter-spacing: 1px;
  }
  .person-role {
    font-family: "Cinzel", Georgia, serif;
    font-size: 17px; color: var(--gold); letter-spacing: 1.5px; margin-top: 2px;
  }
  .contact {
    position: absolute;
    left: 330px; top: 78px;
    font-size: 13.5px; line-height: 1.7; color: var(--text-grey);
  }
  .contact .gap { margin-top: 14px; }
  .contact strong { color: var(--ink); font-weight: 600; }
  .base-band {
    position: absolute; left: 0; right: 0; bottom: 0; height: 16px;
    background: var(--band);
  }
  .base-band .accent {
    position: absolute; left: 260px; top: 0; width: 110px; height: 16px;
    background: var(--gold);
  }
</style>
</head>
<body>
  <section class="card card--front" aria-label="Card front">
    <div class="front-decoration" aria-hidden="true"></div>
    <div class="front-wordmark">
      <div class="wordmark-name">Harcourt Memorials</div>
      <div class="wordmark-rule"></div>
      <div class="site">harcourtmemorials.com.au</div>
    </div>
  </section>

  <section class="card card--back" aria-label="Card back">
    <div class="back-brand">
      <span class="brand-square" aria-hidden="true"></span>
      <span class="wordmark-name">Harcourt<br>Memorials</span>
    </div>
    <div class="brand-rule"></div>
    <div class="person">
      <div class="person-name">Simon Harcourt</div>
      <div class="person-role">Operations Manager</div>
    </div>
    <div class="contact">
      <div>Suite 17, 8 Palfrey Lane</div>
      <div>West Carlow, Sydney NSW 2156</div>
      <div class="gap"><strong>P:</strong> 02 9561 3048 | <strong>M:</strong> 0417293086</div>
      <div>simon@harcourtmemorials.com.au</div>
      <div>www.harcourtmemorials.com.au</div>
    </div>
    <div class="base-band"><span class="accent"></span></div>
  </section>
</body>
</html>
```